Business Card Design

We like to use greens as you will see in our logo (but not TOO much green). We are a Dental Clinic in a somewhat eccentric community. We do not like the dated sharp designs which we see many dentists use. We're looking for something bright and fresh while still maintaining the integrity of the profession. Elegance is not necessarily what we are going for... we need for the design to be "mature" but also up-lifting.

See our logo.
Updates

Project Deadline Extended
Reason: We have 5 designs which we like. But we'd like to see a few more before committing to a design.

Project Deadline Extended
Reason: We are awaiting revisions to this project. We are still welcoming designs while we wait to see if designers are able to provide to us the revisions we require in order to proceed with a selection.

Target Market(s)

Younger families - ages late 20's to early 40's

Industry/Entity Type

Business

Contact Information for Business Card

Corwel T. Banfry DDS 2730 W. Halvert Rd. Ste. 7 Royal Oak, MI 48391 (248)555-0174 FX (248)555-0189 info@BrightwellDentalCareMi.com BrigthwellDentalCareMi.com on the back of the card we need an appointment reminder (For____ Date___ Time____) with "If you are unable to keep your appointment, kindly give 48 hours notice" at the bottom. No use of teeth in the design. DOUBLE SIDED DESIGN

Requirements
Should not have
• The use of pictures of teeth

```html
<!DOCTYPE html>
<html lang="en">
<head>
<meta charset="utf-8">
<title>Brightwell Dental Care – Business Card</title>
<link href="https://fonts.googleapis.com/css2?family=Cinzel:wght@500&family=Source+Sans+3:ital,wght@0,400;0,600;0,700;1,500&display=swap" rel="stylesheet">
<style>
  :root {
    --green: #1e6b3a;
    --green-light: #8cc63f;
    --green-soft: #b9dc8c;
    --ink: #3a3a3a;
    --paper: #ffffff;
    --backdrop: #ebe8e3;
    --box-line: #555555;
  }
  * { margin: 0; padding: 0; box-sizing: border-box; }
  html, body { width: 1200px; height: 1188px; overflow: hidden; }
  body {
    background: var(--backdrop);
    position: relative;
    font-family: "Source Sans 3", "Helvetica Neue", Arial, sans-serif;
    color: var(--ink);
  }
  .card {
    position: absolute;
    width: 914px;
    height: 523px;
    background: var(--paper);
    box-shadow: 0 2px 8px rgba(0,0,0,0.12);
    overflow: hidden;
  }
  .card-front { left: 23px; top: 50px; }
  .card-back { left: 232px; top: 616px; }

  /* front */
  .brand {
    position: absolute; left: 0; top: 0; width: 438px; height: 100%;
    display: flex; flex-direction: column; align-items: center; justify-content: center; gap: 22px;
  }
  .brand-dot { width: 90px; height: 90px; border-radius: 50%; background: var(--green-light); }
  .brand-name {
    font-weight: 700; color: var(--green); font-size: 50px; line-height: 1.05; text-align: center;
  }
  .front-stripe { position: absolute; left: 440px; top: 0; width: 9px; height: 100%; background: var(--green); }
  .front-panel {
    position: absolute; left: 455px; top: 0; right: 0; height: 100%;
    background: var(--green); color: #fff;
  }
  .person { position: absolute; left: 42px; top: 88px; }
  .person-name { font-size: 33px; font-weight: 700; line-height: 1.1; }
  .person-title { font-size: 24px; font-weight: 400; margin-top: 4px; }
  .contact-list { position: absolute; left: 42px; top: 202px; list-style: none; }
  .contact-list li {
    display: flex; align-items: center; gap: 8px;
    font-size: 23px; height: 40.5px;
  }
  .contact-list svg { width: 20px; height: 20px; flex: none; }
  .address { position: absolute; left: 42px; top: 392px; font-size: 23px; line-height: 33px; }

  /* back */
  .back-accent {
    position: absolute; left: 305px; top: 40px; width: 300px; height: 300px;
    border-radius: 50%; background: var(--green-soft); opacity: 0.35;
  }
  .appt-title {
    position: absolute; left: 0; width: 100%; top: 88px; text-align: center;
    font-family: "Cinzel", "Times New Roman", serif; font-weight: 500;
    font-size: 31px; color: var(--green); letter-spacing: 0.5px;
  }
  .field-label { position: absolute; font-size: 24px; line-height: 1; }
  .dots { position: absolute; height: 0; border-bottom: 2px dotted var(--ink); }
  .slot {
    position: absolute; height: 33px; border: 2px solid var(--box-line); border-radius: 4px;
  }
  .day { position: absolute; top: 378px; font-size: 23px; font-weight: 600; line-height: 1; }
  .day-box { position: absolute; top: 373px; width: 56px; height: 33px; border: 2px solid var(--box-line); }
  .notice {
    position: absolute; left: 0; width: 100%; top: 452px; text-align: center;
    font-size: 23px; font-style: italic; font-weight: 500;
  }
</style>
</head>
<body>

<section class="card card-front">
  <div class="brand">
    <div class="brand-dot"></div>
    <div class="brand-name">Brightwell<br>Dental Care</div>
  </div>
  <div class="front-stripe"></div>
  <div class="front-panel">
    <div class="person">
      <div class="person-name">Corwel T. Banfry</div>
      <div class="person-title">DDS</div>
    </div>
    <ul class="contact-list">
      <li>
        <svg viewBox="0 0 20 20"><circle cx="10" cy="10" r="8.5" fill="none" stroke="#fff" stroke-width="1.5"/><path d="M7 5.5l2 2-1 1.5c.6 1.4 1.6 2.4 3 3l1.5-1 2 2-1.2 1.3c-3.6-.5-6.6-3.5-7.1-7.1z" fill="#fff"/></svg>
        (248)555-0174
      </li>
      <li>
        <svg viewBox="0 0 20 20"><rect x="5" y="3" width="10" height="6" fill="#fff"/><rect x="2" y="8" width="16" height="8" rx="1.5" fill="#fff"/><rect x="5" y="11" width="10" height="2" fill="#1e6b3a"/></svg>
        (248)555-0189
      </li>
      <li>
        <svg viewBox="0 0 20 20"><rect x="2" y="5" width="16" height="11" rx="1.5" fill="#fff"/><path d="M2.5 6l7.5 5.5L17.5 6" fill="none" stroke="#1e6b3a" stroke-width="1.5"/></svg>
        info@BrightwellDentalCareMi.com
      </li>
      <li>
        <svg viewBox="0 0 20 20" fill="none" stroke="#fff" stroke-width="1.4"><circle cx="10" cy="10" r="8"/><ellipse cx="10" cy="10" rx="3.5" ry="8"/><path d="M2 10h16M3.5 6h13M3.5 14h13"/></svg>
        BrigthwellDentalCareMi.com
      </li>
    </ul>
    <div class="address">2730 W. Halvert Rd.<br>Ste. 7 Royal Oak, MI 48391</div>
  </div>
</section>

<section class="card card-back">
  <div class="back-accent"></div>
  <h1 class="appt-title">YOUR APPOINTMENT</h1>

  <span class="field-label" style="left:71px; top:158px;">Name :</span>
  <span class="dots" style="left:175px; width:666px; top:178px;"></span>

  <span class="field-label" style="left:71px; top:225px;">Date :</span>
  <span class="dots" style="left:166px; width:228px; top:245px;"></span>
  <span class="field-label" style="left:410px; top:225px;">Time :</span>
  <span class="dots" style="left:488px; width:245px; top:245px;"></span>
  <span class="field-label" style="left:741px; top:225px;">am / pm</span>

  <span class="field-label" style="left:71px; top:288px;">Next Appointment</span>
  <span class="slot" style="left:324px; width:166px; top:283px;"></span>
  <span class="slot" style="left:503px; width:164px; top:283px;"></span>
  <span class="slot" style="left:677px; width:166px; top:283px;"></span>

  <span class="day" style="left:68px;">MON</span><span class="day-box" style="left:145px;"></span>
  <span class="day" style="left:212px;">TUE</span><span class="day-box" style="left:273px;"></span>
  <span class="day" style="left:341px;">WED</span><span class="day-box" style="left:414px;"></span>
  <span class="day" style="left:482px;">THU</span><span class="day-box" style="left:546px;"></span>
  <span class="day" style="left:614px;">FRI</span><span class="day-box" style="left:667px;"></span>
  <span class="day" style="left:733px;">SAT</span><span class="day-box" style="left:790px;"></span>

  <p class="notice">If you are unable to keep your appointment, kindly give 48 hours notice</p>
</section>

</body>
</html>
```